Business Cards Design for the electrical wholesaler: clean bold dynamic :)

We need a business card design that would follow our latest brand guidelines. As an electrical wholesaler we want to bring a fresh look and feel into the industry. The design should be clean bold and dynamic. It should come alive with the renewed energy of our green colour. Our grey colour should keep things balanced and complement the notion of maturity and responsibility. We employ Lato as a corporate font however are not bound by this font and we’re open to interpretation here.

Target Market(s)

Electrical contractors

Industry/Entity Type

Business

Contact Information for Business Card

Logo
Name & Surname: Halyna Dorosh
Job Title: Director of Marketing
Email: halya.dorosh@quillmail.example
Cell phone: XXX.XXX.XXXX
Address: 20517 - 87 Ave. Edmonton, AB, Canada. T6K 4N8
Business Phone: 780.555.0184
Website: www.brovix.example

Font styles to use
Other font styles liked:
• Lato

Requirements
Must have
• Logo & website
Nice to have
• Brand elements - some of them you may find in the attached Brand Guidelines (e.g. three lines on the background signifying "W")

```html
<!DOCTYPE html>
<html lang="en">
<head>
<meta charset="utf-8">
<title>Brovix Business Cards</title>
<link rel="stylesheet" href="https://fonts.googleapis.com/css2?family=Lato:wght@400;700&display=swap">
<style>
  :root {
    --green: #8dc63f;
    --grey: #4d4d4f;
    --grey-soft: #6d6e71;
    --white: #ffffff;
    --stage: #e8ecf0;
  }
  * { margin: 0; padding: 0; box-sizing: border-box; }
  html, body { width: 1200px; height: 1000px; overflow: hidden; }
  body {
    background: var(--stage);
    font-family: "Lato", sans-serif;
    color: var(--grey);
    position: relative;
  }
  .card {
    position: absolute;
    background: var(--white);
    overflow: hidden;
  }
  .card--rounded { border-radius: 28px; }
  .card--a { left: 64px;  top: 60px;  width: 507px; height: 288px; }
  .card--b { left: 64px;  top: 428px; width: 507px; height: 288px; }
  .card--c { left: 624px; top: 283px; width: 512px; height: 292px; }
  .card--d { left: 624px; top: 640px; width: 512px; height: 292px; }

  /* Brand lockup */
  .brand {
    position: absolute;
    display: flex;
    flex-direction: column;
    align-items: flex-end;
  }
  .brand__row { display: flex; align-items: center; gap: 10px; }
  .brand__mark { background: var(--green); }
  .brand__name {
    font-weight: 400;
    color: var(--grey);
    line-height: 1;
    letter-spacing: -0.5px;
  }
  .brand__tag {
    font-weight: 700;
    color: var(--grey);
    text-transform: uppercase;
    letter-spacing: 1px;
  }
  .brand--front { left: 50%; top: 50%; transform: translate(-50%, -54%); }
  .brand--front .brand__mark { width: 46px; height: 46px; }
  .brand--front .brand__name { font-size: 66px; }
  .brand--front .brand__tag { font-size: 11px; margin-top: 4px; }

  .brand--back { right: 32px; top: 32px; }
  .brand--back .brand__mark { width: 26px; height: 26px; }
  .brand--back .brand__name { font-size: 38px; }
  .brand--back .brand__tag { font-size: 7px; margin-top: 2px; }

  /* Back side */
  .card__band { position: absolute; inset: 0; width: 100%; height: 100%; }
  .person { position: absolute; left: 27px; top: 80px; width: 195px; }
  .person__name { font-size: 26px; font-weight: 400; color: var(--grey); line-height: 1.1; }
  .person__title { font-size: 15px; color: var(--grey-soft); margin-top: 4px; }
  .person__rule { height: 2px; background: var(--grey-soft); margin-top: 10px; width: 194px; }

  .contact { position: absolute; left: 27px; top: 181px; list-style: none; }
  .contact__item {
    display: flex; align-items: center; gap: 10px;
    font-size: 17px; color: var(--grey); height: 24px;
  }
  .contact__icon { width: 13px; height: 13px; fill: var(--grey); flex: none; }

  .address {
    position: absolute; right: 32px; top: 150px;
    text-align: right; color: var(--white);
    font-size: 15px; line-height: 19px; font-style: normal;
  }
  .address__icon { width: 12px; height: 14px; fill: var(--white); vertical-align: -1px; margin-right: 4px; }
  .website {
    position: absolute; right: 32px; top: 244px;
    font-size: 14px; color: var(--grey);
  }
</style>
</head>
<body>

<svg width="0" height="0" style="position:absolute" aria-hidden="true">
  <defs>
    <symbol id="icon-mobile" viewBox="0 0 24 24"><path d="M6.6 10.8a15.1 15.1 0 0 0 6.6 6.6l2.2-2.2a1 1 0 0 1 1-.25 11.4 11.4 0 0 0 3.6.57 1 1 0 0 1 1 1V20a1 1 0 0 1-1 1A17 17 0 0 1 3 4a1 1 0 0 1 1-1h3.5a1 1 0 0 1 1 1c0 1.25.2 2.45.57 3.57a1 1 0 0 1-.25 1z"/></symbol>
    <symbol id="icon-desk" viewBox="0 0 24 24"><path d="M2 8c2-3 6-4 10-4s8 1 10 4l-3 2-2-3H7L5 10z"/><path d="M6 11h12l2 9H4zM12 13a3 3 0 1 0 0 6 3 3 0 0 0 0-6z"/></symbol>
    <symbol id="icon-mail" viewBox="0 0 24 24"><path d="M2 5h20v14H2zm2 2v.5l8 5 8-5V7l-8 5z"/></symbol>
    <symbol id="icon-pin" viewBox="0 0 20 24"><path d="M10 0a8 8 0 0 0-8 8c0 6 8 16 8 16s8-10 8-16a8 8 0 0 0-8-8zm0 11a3 3 0 1 1 0-6 3 3 0 0 1 0 6z"/></symbol>
  </defs>
</svg>

<!-- Front, rounded -->
<section class="card card--rounded card--a">
  <div class="brand brand--front">
    <div class="brand__row"><span class="brand__mark"></span><span class="brand__name">brovix</span></div>
    <span class="brand__tag">Electrical Wholesalers</span>
  </div>
</section>

<!-- Back, rounded -->
<section class="card card--rounded card--b">
  <svg class="card__band" viewBox="0 0 507 288" preserveAspectRatio="none" aria-hidden="true">
    <path d="M179 0H507V288H288C258 212 216 92 179 0Z" fill="var(--green)"/>
  </svg>
  <div class="brand brand--back">
    <div class="brand__row"><span class="brand__mark"></span><span class="brand__name">brovix</span></div>
    <span class="brand__tag">Electrical Wholesalers</span>
  </div>
  <div class="person">
    <h1 class="person__name">Halyna Dorosh</h1>
    <p class="person__title">Director of Marketing</p>
    <div class="person__rule"></div>
  </div>
  <ul class="contact">
    <li class="contact__item"><svg class="contact__icon"><use href="#icon-mobile"/></svg>780.555.0184</li>
    <li class="contact__item"><svg class="contact__icon"><use href="#icon-desk"/></svg>780.555.0184</li>
    <li class="contact__item"><svg class="contact__icon"><use href="#icon-mail"/></svg>halya.dorosh@quillmail.example</li>
  </ul>
  <address class="address"><svg class="address__icon"><use href="#icon-pin"/></svg>20517 - 87 Ave.<br>Edmonton, AB,<br>Canada. T6K 4N8</address>
  <p class="website">www.brovix.example</p>
</section>

<!-- Front, square corners -->
<section class="card card--c">
  <div class="brand brand--front">
    <div class="brand__row"><span class="brand__mark"></span><span class="brand__name">brovix</span></div>
    <span class="brand__tag">Electrical Wholesalers</span>
  </div>
</section>

<!-- Back, square corners -->
<section class="card card--d">
  <svg class="card__band" viewBox="0 0 512 292" preserveAspectRatio="none" aria-hidden="true">
    <path d="M182 0H512V292H291C261 215 219 93 182 0Z" fill="var(--green)"/>
  </svg>
  <div class="brand brand--back">
    <div class="brand__row"><span class="brand__mark"></span><span class="brand__name">brovix</span></div>
    <span class="brand__tag">Electrical Wholesalers</span>
  </div>
  <div class="person">
    <h2 class="person__name">Halyna Dorosh</h2>
    <p class="person__title">Director of Marketing</p>
    <div class="person__rule"></div>
  </div>
  <ul class="contact">
    <li class="contact__item"><svg class="contact__icon"><use href="#icon-mobile"/></svg>780.555.0184</li>
    <li class="contact__item"><svg class="contact__icon"><use href="#icon-desk"/></svg>780.555.0184</li>
    <li class="contact__item"><svg class="contact__icon"><use href="#icon-mail"/></svg>halya.dorosh@quillmail.example</li>
  </ul>
  <address class="address"><svg class="address__icon"><use href="#icon-pin"/></svg>20517 - 87 Ave.<br>Edmonton, AB,<br>Canada. T6K 4N8</address>
  <p class="website">www.brovix.example</p>
</section>

</body>
</html>
```